Business Card Design - Photographer

I am a landscape photographer and I require a business card design. 

I require two designs:
1)  a double sided business card
 and
b)  a single sided business card 

The single sided design can either be the same as the double sided (with just one side having all the information)....or it can be an entire new design. Its up to you.

My corporate colours are (CMYK):

Blue   69, 32, 0, 0
Grey  72,  64,  47,  31
Green  32,  2,  91,  0
Yellow   0, 19, 92, 0
Orange  0, 39, 75, 0

Colour space in final file should be in CMYK.

The details that need to be included on the card:

- Use the provided Logo
- Name: Wiktor Baranowski
- Email:   sales@vistalumeworks.com.au
- Website:    vistalumeworks.com.au
- Twitter:    twitter.com/vistalumeworks
- Facebook:   facebook.com/vistalumeworks
- Mobile  0417 539 662

Please use the attached template to design the logo to the specified size, including the marked bleed lines. I have also attached my logo in PNG (transparent background) and ai format for you to use.

The final file should be:
- Photoshop version with layers so I can edit the name/text etc. All non vector files should be high resolution at 1039 x 697 pixels at 300 dpi.

I also require a file as:
- Vector based PDF

Anyway questions please contact me.

Thank you

Industry/Entity Type

Landscape

Logo styles of interest
Pictorial/Combination Logo
Abstract Logo
Wordmark Logo
Lettermark Logo
Requirements
Must have
• The details that need to be included on the card:

- Use the provided Logo
- Name: Wiktor Baranowski
- Email: sales@vistalumeworks.com.au
- Website: vistalumeworks.com.au
- Twitter: twitter.com/vistalumeworks
- Facebook: facebook.com/vistalumeworks
- Mobile 0417 539 662

```html
<!DOCTYPE html>
<html lang="en">
<head>
<meta charset="utf-8">
<title>Vistalume Works – Business Cards</title>
<link rel="stylesheet" href="https://fonts.googleapis.com/css2?family=Cinzel:wght@400;600;700&display=swap">
<style>
  :root {
    --board: #808084;
    --top-strip: #ffffff;
    --card: #ffffff;
    --yellow: #fdc800;
    --blue: #3d8fd1;
    --grey: #3b3f52;
    --shadow: rgba(0, 0, 0, 0.28);
  }
  * { margin: 0; padding: 0; box-sizing: border-box; }
  html, body {
    width: 928px; height: 1200px; overflow: hidden;
    background: var(--board);
    font-family: "Cinzel", "Times New Roman", serif;
  }
  .board { position: relative; width: 928px; height: 1200px; }
  .board__strip { position: absolute; left: 0; top: 0; width: 928px; height: 61px; background: var(--top-strip); }

  .card {
    position: absolute; left: 81px; width: 776px; height: 443px;
    background: var(--card); border-radius: 22px; overflow: hidden;
    box-shadow: 4px 6px 10px var(--shadow);
  }
  .card--front { top: 151px; }
  .card--back { top: 707px; }

  .card__band { position: absolute; left: 0; top: 0; width: 100%; height: 138px; background: var(--yellow); }
  .card__rule { position: absolute; left: 0; top: 138px; width: 100%; height: 4px; background: var(--blue); }
  .card__arc {
    position: absolute; left: 26px; top: 47px; width: 274px; height: 274px;
    border-radius: 50%; background: var(--card);
  }
  .card__mark {
    position: absolute; left: 67px; top: 80px; width: 208px; height: 208px;
    border-radius: 50%; background: var(--grey);
  }

  .brand { position: absolute; left: 318px; top: 170px; width: 426px; text-align: center; color: var(--grey); }
  .brand__name { font-size: 37px; font-weight: 600; line-height: 44px; letter-spacing: 0.5px; white-space: nowrap; }
  .brand__line { height: 2px; background: var(--grey); margin-top: 4px; }
  .brand__tagline { font-size: 15px; font-weight: 700; letter-spacing: 3.4px; margin-top: 10px; }

  .web-front {
    position: absolute; left: 318px; top: 386px; width: 426px; text-align: center;
    color: var(--blue); font-weight: 600; white-space: nowrap;
  }
  .web-front__small { font-size: 14px; }
  .web-front__big { font-size: 20px; font-weight: 700; }

  .contacts {
    position: absolute; left: 0; top: 328px; width: 100%; text-align: center;
    color: var(--grey); font-size: 15.5px; line-height: 29px; white-space: nowrap;
  }
  .contacts__label { color: var(--blue); font-size: 17px; }
  .contacts__gap { display: inline-block; width: 12px; }

  .web-back {
    position: absolute; left: 0; top: 402px; width: 100%; text-align: center;
    color: var(--blue); font-size: 21px; font-weight: 700; letter-spacing: 0.5px;
  }
</style>
</head>
<body>
<main class="board">
  <div class="board__strip"></div>

  <section class="card card--front" aria-label="Card front">
    <div class="card__band"></div>
    <div class="card__rule"></div>
    <div class="card__arc"></div>
    <div class="card__mark"></div>
    <div class="brand">
      <div class="brand__name">VISTALUME WORKS</div>
      <div class="brand__line"></div>
      <div class="brand__tagline">FINE ART PHOTOGRAPHY</div>
    </div>
    <div class="web-front">
      <span class="web-front__small">www.</span><span class="web-front__big">VISTALUMEWORKS</span><span class="web-front__small">.com.au</span>
    </div>
  </section>

  <section class="card card--back" aria-label="Card back">
    <div class="card__band"></div>
    <div class="card__rule"></div>
    <div class="card__arc"></div>
    <div class="card__mark"></div>
    <div class="brand">
      <div class="brand__name">VISTALUME WORKS</div>
      <div class="brand__line"></div>
      <div class="brand__tagline">FINE ART PHOTOGRAPHY</div>
    </div>
    <div class="contacts">
      <div><span class="contacts__label">E</span> : sales@vistalumeworks.com.au<span class="contacts__gap"></span><span class="contacts__label">M</span> : 0417 539 662</div>
      <div><span class="contacts__label">T</span> : twitter.com/vistalumeworks<span class="contacts__gap"></span><span class="contacts__label">F</span> : facebook.com/vistalumeworks</div>
    </div>
    <div class="web-back">WWW.VISTALUMEWORKS.COM.AU</div>
  </section>
</main>
</body>
</html>
```